Letterhead for a Natural Hair Run

We need a letterhead design with the logo uploaded entitled 'Tidewalk Five'. This run is a natural 5K run seeking to promote the acceptance of natural beauty in every aspect of society encompassing one's ethnic roots and its connection to a healthy lifetstyle. We would like to see designs coordinating with our logo. The design should be fun and exciting!

Industry/Entity Type

Hair

Font styles to use
Serif
Sans Serif

Requirements
Must have
• Please included this information on the letter head:
• P.O. Box K7142
• Port Halden, Coralis
• Phone: (242) 618-9027
• Email: tidewalker519@brinkmail.example

```html
<!DOCTYPE html>
<html lang="en">
<head>
<meta charset="utf-8">
<title>Tidewalk Five Letterhead</title>
<link href="https://fonts.googleapis.com/css2?family=Arimo:wght@400;700&display=swap" rel="stylesheet">
<style>
  :root {
    --paper: #ffffff;
    --sun: #f4e24f;
    --lagoon: #19b9d6;
    --icon: #ffffff;
  }
  * { margin: 0; padding: 0; box-sizing: border-box; }
  html, body { width: 960px; height: 1200px; overflow: hidden; background: var(--paper); }
  .letterhead {
    position: relative;
    width: 960px;
    height: 1200px;
    background: var(--paper);
    font-family: "Arimo", Arial, sans-serif;
  }
  .brand {
    position: absolute;
    top: 70px;
    left: 0;
    width: 960px;
    display: flex;
    justify-content: center;
    align-items: center;
    gap: 14px;
  }
  .brand-dot {
    width: 24px;
    height: 24px;
    border-radius: 50%;
    background: var(--lagoon);
  }
  .brand-name {
    font-size: 38px;
    font-weight: 400;
    line-height: 1;
    color: var(--lagoon);
  }
  .accent-band {
    position: absolute;
    left: 0;
    top: 1076px;
    width: 960px;
    height: 21px;
    background: var(--sun);
  }
  .contact-bar {
    position: absolute;
    left: 0;
    top: 1097px;
    width: 960px;
    height: 103px;
    background: var(--lagoon);
  }
  .contact-icon {
    position: absolute;
    width: 28px;
    height: 28px;
    fill: var(--icon);
  }
  .contact-text {
    position: absolute;
    color: var(--sun);
    font-size: 18px;
    line-height: 22px;
    white-space: nowrap;
  }
  .row-top { top: 17px; }
  .row-bottom { top: 57px; }
  .icon-city { left: 77px; top: 14px; }
  .text-city { left: 145px; }
  .icon-box { left: 362px; top: 14px; }
  .text-box { left: 429px; }
  .icon-phone { left: 622px; top: 14px; }
  .text-phone { left: 690px; }
  .icon-email { left: 308px; top: 54px; }
  .text-email { left: 376px; }
</style>
</head>
<body>
<main class="letterhead">
  <header class="brand">
    <span class="brand-dot"></span>
    <span class="brand-name">Tidewalk Five</span>
  </header>

  <div class="accent-band"></div>

  <footer class="contact-bar">
    <svg class="contact-icon icon-city" viewBox="0 0 24 24" aria-hidden="true"><path d="M12 3 2 12h3v9h5v-6h4v6h5v-9h3z"/></svg>
    <span class="contact-text row-top text-city">Port Halden, Coralis</span>

    <svg class="contact-icon icon-box" viewBox="0 0 24 24" aria-hidden="true"><path d="M3 8l9-4 9 4v10l-9 3-9-3z M5 9v8l7 2.3V11z"/></svg>
    <span class="contact-text row-top text-box">P.O. Box K7142</span>

    <svg class="contact-icon icon-phone" viewBox="0 0 24 24" aria-hidden="true"><path d="M6.6 10.8a15 15 0 0 0 6.6 6.6l2.2-2.2c.3-.3.7-.4 1-.2 1.1.4 2.3.6 3.6.6.6 0 1 .4 1 1V20c0 .6-.4 1-1 1A17 17 0 0 1 3 4c0-.6.4-1 1-1h3.5c.6 0 1 .4 1 1 0 1.3.2 2.5.6 3.6.1.3 0 .7-.2 1z"/></svg>
    <span class="contact-text row-top text-phone">Phone: (242) 618-9027</span>

    <svg class="contact-icon icon-email" viewBox="0 0 24 24" aria-hidden="true"><path d="M12 2 3 9v12h18V9z M5 10.5l7 5 7-5V19H5z"/></svg>
    <span class="contact-text row-bottom text-email">Email: tidewalker519@brinkmail.example</span>
  </footer>
</main>
</body>
</html>
```